Profesional personal website needs design and business card

I need a business card with my professional name as a logo "Dorian Vitality" for my business. I am a Wellness Coach, consultant and trainer. So it should be professional, wellness oriented and modern.

Target Market(s)

Private clients, governments, corporations. Luxury and high market.

Industry/Entity Type

Health And Wellness

Contact Information for Business Card

Dorian Vitality should be the logo

Colors

Designer to choose colors to be used in the design.

Requirements
Must have
• Dorian Vitality
• Name: Tomás Lirandel
• Wellness Coach, Consultant & Trainer.
• Website: www.dorianvitality-example.com
• Phone:
• Spain (+34) 612 480 317
• (USA) +1 (555) 610 4829
Nice to have
• The most important is the design of "Dorian Vitality", as this is going to be my personal brand logo. It should be professional, wellness, high end and actual.
Should not have
• no golds, no baroque style..

```html
<!DOCTYPE html>
<html lang="en">
<head>
<meta charset="utf-8">
<title>Dorian Vitality — Business Card</title>
<link rel="stylesheet" href="https://fonts.googleapis.com/css2?family=Poppins:wght@500&family=Roboto:wght@400;700&display=swap">
<style>
  :root {
    --brand-blue: #1a7dad;
    --accent-blue: #27a6df;
    --ink: #111111;
    --paper: #ffffff;
  }
  html, body {
    margin: 0;
    padding: 0;
    width: 1000px;
    height: 1200px;
    overflow: hidden;
    background: var(--paper);
  }
  .sheet { display: block; width: 1000px; height: 1200px; }
  .card-bg { fill: var(--paper); }
  .band { fill: var(--brand-blue); }
  .stripe-blue { stroke: var(--brand-blue); stroke-width: 20; fill: none; }
  .stripe-white { stroke: var(--paper); stroke-width: 20; fill: none; }
  .dashes { stroke-dasharray: 20 19; }
  .diamond { fill: var(--paper); }
  .brand-mark { fill: var(--brand-blue); }
  .brand-name {
    font-family: "Roboto", sans-serif;
    font-weight: 700;
    font-size: 66px;
    fill: var(--brand-blue);
  }
  .website {
    font-family: "Roboto", sans-serif;
    font-weight: 400;
    font-size: 31px;
    fill: var(--ink);
  }
  .person-name {
    font-family: "Roboto", sans-serif;
    font-weight: 700;
    font-size: 84px;
    fill: var(--accent-blue);
  }
  .person-role {
    font-family: "Poppins", sans-serif;
    font-weight: 500;
    font-size: 25px;
    fill: var(--ink);
  }
  .phone-line {
    font-family: "Roboto", sans-serif;
    font-weight: 400;
    font-size: 36px;
    fill: var(--ink);
  }
  .phone-badge { fill: var(--accent-blue); }
  .phone-glyph { fill: var(--ink); }
</style>
</head>
<body>
<svg class="sheet" viewBox="0 0 1750 2100" xmlns="http://www.w3.org/2000/svg">
  <defs>
    <clipPath id="front-clip"><rect x="218" y="126" width="1317" height="878"/></clipPath>
    <clipPath id="back-clip"><rect x="218" y="1121" width="1317" height="842"/></clipPath>
  </defs>

  <!-- Front of card -->
  <g class="card-front" clip-path="url(#front-clip)">
    <rect class="card-bg" x="218" y="126" width="1317" height="878"/>
    <polygon class="band" points="845,126 1535,126 1535,355 885,1004 218,1004 218,753"/>
    <line class="stripe-blue" x1="205" y1="722" x2="430" y2="497"/>
    <line class="stripe-blue dashes" x1="440" y1="487" x2="840" y2="87"/>
    <line class="stripe-blue" x1="931" y1="1010" x2="1327" y2="608"/>
    <line class="stripe-blue dashes" x1="1341" y1="595" x2="1570" y2="366"/>
    <polygon class="diamond" points="876,152 1272,548 876,944 480,548"/>

    <g class="brand-lockup">
      <circle class="brand-mark" cx="876" cy="440" r="52"/>
      <text class="brand-name" x="876" y="578" text-anchor="middle">Dorian Vitality</text>
    </g>
    <text class="website" x="876" y="742" text-anchor="middle">www.dorianvitality-example.com</text>
  </g>

  <!-- Back of card -->
  <g class="card-back" clip-path="url(#back-clip)">
    <rect class="card-bg" x="218" y="1121" width="1317" height="842"/>
    <polygon class="band" points="218,1121 852,1121 218,1730"/>
    <line class="stripe-white" x1="205" y1="1698" x2="437" y2="1474"/>
    <line class="stripe-white dashes" x1="447" y1="1464" x2="870" y2="1057"/>
    <polygon class="band" points="1535,1348 1535,1963 893,1963"/>
    <line class="stripe-white" x1="935" y1="1975" x2="1331" y2="1586"/>
    <line class="stripe-white dashes" x1="1343" y1="1574" x2="1570" y2="1355"/>

    <text class="person-name" x="1415" y="1310" text-anchor="end">Tomás Lirandel</text>
    <text class="person-role" x="1412" y="1352" text-anchor="end">Wellness Coach, Consultant &amp; Trainer</text>

    <g class="contact-phone">
      <circle class="phone-badge" cx="366" cy="1712" r="38"/>
      <path class="phone-glyph" transform="translate(392 1686) scale(-2.2 2.2)" d="M6.62 10.79c1.44 2.83 3.76 5.14 6.59 6.59l2.2-2.2c.27-.27.67-.36 1.02-.24 1.12.37 2.33.57 3.57.57.55 0 1 .45 1 1V20c0 .55-.45 1-1 1-9.39 0-17-7.61-17-17 0-.55.45-1 1-1h3.5c.55 0 1 .45 1 1 0 1.25.2 2.450.57 3.57.11.35.03.74-.25 1.02l-2.2 2.2z"/>
      <text class="phone-line" x="450" y="1696">Spain  : (+34) 612 480 317</text>
      <text class="phone-line" x="450" y="1739">USA    : +1 (555) 610 4829</text>
    </g>
  </g>
</svg>
</body>
</html>
```